American cannabis tech company business card design

Pavrel.com is seeking a modern, professional, and brand-aligned business card that represents our company and its core values: Mission, Story, Values, and Impact. As an innovative cannabis company, we want a business card that is not only visually appealing but also serves as a representation of who we are and what we stand for.

Project Scope: Design a double-sided business card that integrates our brand identity and core values. Incorporate our key brand elements, ensuring a sleek and contemporary aesthetic. Visually reflect our core values (Mission, Story, Values, Impact) in a way that is engaging yet professional.

Target Market(s)

Vendors, third parties,

Contact Information for Business Card

Contact details (name, title, email, phone, website, etc.)

Font styles to use
Other font styles liked:
• Caslon, Centra

Colors

Designer to choose colors to be used in the design.

Requirements
Must have
• Pavrel.com logo and branding A creative yet clean way to integrate our core values (Mission, Story, Values, Impact) Modern typography and a well-structured layout
Nice to have
• forest green, grey, white, black
Should not have
• references to marijuana, leafs, plants, or related product

```html
<!DOCTYPE html>
<html lang="en">
<head>
<meta charset="utf-8">
<title>Pavrel.com Business Card</title>
<link rel="stylesheet" href="https://fonts.googleapis.com/css2?family=Libre+Caslon+Text:wght@400;700&family=Arimo:wght@400&display=swap">
<style>
  :root {
    --backdrop: #2a2a2a;
    --forest: #1a311b;
    --paper: #ffffff;
    --cream: #fcf9f4;
    --sage: #b9c6b5;
    --ink: #111111;
    --rule: #3d4a3e;
    --serif: "Libre Caslon Text", Georgia, serif;
    --sans: "Arimo", Arial, sans-serif;
  }
  * { box-sizing: border-box; margin: 0; padding: 0; }
  html, body { width: 1200px; height: 939px; overflow: hidden; }
  body { background: var(--backdrop); position: relative; font-family: var(--serif); }

  .card {
    position: absolute;
    width: 620px;
    height: 354px;
    border-radius: 22px;
  }
  .card--front { left: 150px; top: 95px; background: var(--forest); }
  .card--back { left: 430px; top: 490px; background: var(--paper); }

  .wordmark {
    position: absolute;
    font-family: var(--serif);
    font-weight: 700;
    letter-spacing: 1px;
    line-height: 1;
  }
  .card--front .wordmark {
    color: var(--cream);
    font-size: 100px;
    left: 0; right: 0; top: 100px;
    text-align: center;
  }
  .card--back .wordmark {
    color: var(--forest);
    font-size: 52px;
    left: 52px; top: 150px;
  }

  .values {
    position: absolute;
    left: 0; right: 0; top: 250px;
    display: flex;
    justify-content: center;
    align-items: center;
    gap: 18px;
    list-style: none;
    font-family: var(--sans);
    font-size: 13px;
    letter-spacing: 4px;
    text-transform: uppercase;
    color: var(--sage);
  }
  .values__item + .values__item::before {
    content: "";
    display: inline-block;
    width: 5px; height: 5px;
    border-radius: 50%;
    background: var(--sage);
    margin-right: 18px;
    vertical-align: middle;
    position: relative;
    top: -2px;
  }

  .divider {
    position: absolute;
    left: 305px; top: 78px;
    width: 1px; height: 210px;
    background: var(--rule);
  }

  .contact {
    position: absolute;
    left: 335px; top: 80px;
    color: var(--ink);
  }
  .contact__name {
    font-size: 22px;
    font-weight: 700;
    color: var(--forest);
    letter-spacing: .3px;
  }
  .contact__title {
    font-family: var(--sans);
    font-size: 15px;
    margin: 6px 0 12px 8px;
  }
  .contact__list { list-style: none; margin-left: 8px; }
  .contact__item {
    display: flex;
    align-items: center;
    gap: 12px;
    font-size: 16px;
    height: 24px;
  }
  .contact__item svg { width: 16px; height: 16px; fill: var(--ink); flex: none; }
  .contact__address {
    margin: 16px 0 0 8px;
    font-size: 16px;
    line-height: 1.35;
  }
</style>
</head>
<body>
  <section class="card card--front" aria-label="Business card front">
    <div class="wordmark">PAVREL</div>
    <ul class="values" aria-label="Core values">
      <li class="values__item">Mission</li>
      <li class="values__item">Story</li>
      <li class="values__item">Values</li>
      <li class="values__item">Impact</li>
    </ul>
  </section>

  <section class="card card--back" aria-label="Business card back">
    <div class="wordmark">PAVREL</div>
    <div class="divider"></div>
    <div class="contact">
      <p class="contact__name">Daniel Harlow</p>
      <p class="contact__title">Owner</p>
      <ul class="contact__list">
        <li class="contact__item">
          <svg viewBox="0 0 24 24" aria-hidden="true"><path d="M6.6 10.8a15.5 15.5 0 0 0 6.6 6.6l2.2-2.2a1 1 0 0 1 1-.25 11.4 11.4 0 0 0 3.6.57 1 1 0 0 1 1 1V20a1 1 0 0 1-1 1A17 17 0 0 1 3 4a1 1 0 0 1 1-1h3.5a1 1 0 0 1 1 1c0 1.25.2 2.45.57 3.57a1 1 0 0 1-.25 1z"/></svg>
          044-555 010 274
        </li>
        <li class="contact__item">
          <svg viewBox="0 0 24 24" aria-hidden="true"><path d="M2 5h20v14H2z M2 5l10 8 10-8" fill="none" stroke="#111" stroke-width="2"/><path d="M2 5h20l-10 8z"/></svg>
          hello@pavrel.com
        </li>
        <li class="contact__item">
          <svg viewBox="0 0 24 24" aria-hidden="true"><circle cx="12" cy="12" r="10" fill="none" stroke="#111" stroke-width="2"/><path d="M2 12h20M12 2c3 3 3 17 0 20M12 2c-3 3-3 17 0 20" fill="none" stroke="#111" stroke-width="1.6"/></svg>
          www.pavrel.com
        </li>
      </ul>
      <p class="contact__address">58 Larkspur Avenue, Suite 4<br>80204, United States</p>
    </div>
  </section>
</body>
</html>
```